Verodex business card

Business card for sustainable investment company called "Verodex". Verodex is an exchange platform selling carbon credits between buyers and sellers. Carbon Credits are an environmental commodity for reducing global carbon emissions.

the card should obviously have our logo and the theme should be sustainability/environment mixed with a trading platform.

Contact Information for Business Card

Logo, Name, Title, Phone, Email

Colors
0054AA
0677BA
7BADD7
CADEEF
E8F1F8
0094D4
00A9DD
6FCCEA
C7EBF8
E9F6FB
00AB8E
00BBA5
67D7C9
C6EFE9
E9F9F6
59FF00
82FF00
B8FF75
E3FFCB
F4FFEA

```html
<!DOCTYPE html>
<html lang="en">
<head>
<meta charset="utf-8">
<title>Verodex business card</title>
<link href="https://fonts.googleapis.com/css2?family=Montserrat:wght@400;500;700&display=swap" rel="stylesheet">
<style>
  :root {
    --backdrop: #2b2c2f;
    --navy: #17284d;
    --ink: #243556;
    --blue-deep: #4a7cc2;
    --blue-mid: #4f9fcf;
    --aqua: #66c9d8;
    --accent: #0677BA;
    --accent-light: #6FCCEA;
    --paper: #ffffff;
  }
  * { margin: 0; padding: 0; box-sizing: border-box; }
  html, body { width: 1200px; height: 801px; overflow: hidden; }
  body {
    background: var(--backdrop);
    font-family: "Montserrat", Arial, sans-serif;
    position: relative;
  }
  .card {
    position: absolute;
    width: 540px;
    height: 309px;
    border-radius: 14px;
    overflow: hidden;
  }
  .card--front {
    left: 40px; top: 246px;
    background: linear-gradient(30deg, var(--aqua) 0%, var(--blue-mid) 50%, var(--blue-deep) 100%);
    display: flex; align-items: center; justify-content: center; gap: 14px;
  }
  .card--back { left: 620px; top: 246px; background: var(--paper); }

  .brand-mark { width: 26px; height: 26px; border-radius: 4px; }
  .card--front .brand-mark { background: var(--paper); }
  .card--front .brand-name {
    color: var(--paper); font-weight: 700; font-size: 46px; letter-spacing: 1px;
  }

  .back-brand {
    position: absolute; left: 34px; top: 58px;
    display: flex; align-items: center; gap: 12px;
  }
  .card--back .brand-mark { background: var(--accent); width: 22px; height: 22px; }
  .card--back .brand-name {
    color: var(--navy); font-weight: 700; font-size: 38px; letter-spacing: 1px;
  }

  .person { position: absolute; left: 150px; top: 140px; }
  .person__name { color: var(--navy); font-weight: 700; font-size: 26px; letter-spacing: 0.5px; line-height: 1; }
  .person__title { color: var(--ink); font-size: 15px; margin-top: 4px; }
  .person__rule {
    width: 70px; height: 2px; margin-top: 6px;
    background: linear-gradient(90deg, var(--accent-light), var(--accent));
  }
  .contacts { list-style: none; margin-top: 10px; }
  .contacts li {
    display: flex; align-items: center; gap: 8px;
    color: var(--ink); font-size: 14px; line-height: 22px;
  }
  .contacts svg { width: 14px; height: 14px; flex: none; }

  .divider {
    position: absolute; left: 372px; top: 170px; width: 1.5px; height: 44px;
    background: linear-gradient(180deg, var(--accent), var(--accent-light));
  }
  .address {
    position: absolute; left: 388px; top: 168px;
    color: var(--ink); font-size: 13px; line-height: 22px; font-style: normal;
  }
</style>
</head>
<body>
  <section class="card card--front" aria-label="Card front">
    <span class="brand-mark"></span>
    <span class="brand-name">VERODEX</span>
  </section>

  <section class="card card--back" aria-label="Card back">
    <div class="back-brand">
      <span class="brand-mark"></span>
      <span class="brand-name">VERODEX</span>
    </div>

    <div class="person">
      <p class="person__name">MARCUS HALE</p>
      <p class="person__title">Founder</p>
      <div class="person__rule"></div>
      <ul class="contacts">
        <li>
          <svg viewBox="0 0 16 16" aria-hidden="true"><path d="M4 1.5l2.5 3-1.5 1.5a9 9 0 0 0 5 5l1.5-1.5 3 2.5-1.5 2.5C7.5 14.5 1.5 8.5 1.5 3z" fill="#0677BA"/></svg>
          303-555-0142
        </li>
        <li>
          <svg viewBox="0 0 16 16" aria-hidden="true"><rect x="1" y="3" width="14" height="10" rx="1" fill="#0094D4"/><path d="M1.5 3.5L8 9l6.5-5.5" stroke="#fff" stroke-width="1.3" fill="none"/></svg>
          info@verodex.com
        </li>
        <li>
          <svg viewBox="0 0 16 16" aria-hidden="true"><circle cx="8" cy="8" r="7" fill="#0677BA"/><path d="M1 8h14M8 1c-3 3.5-3 10.5 0 14M8 1c3 3.5 3 10.5 0 14" stroke="#fff" stroke-width="0.9" fill="none"/></svg>
          www.verodex.com
        </li>
      </ul>
    </div>

    <div class="divider"></div>
    <address class="address">18 Harbor Lane,<br>Ashford</address>
  </section>
</body>
</html>
```